Designing a Mailer/Courier bag with our Company Logo for Product Shipping

We need a quirky Mailer/Courier Bag for our company, Renard Céleste. As a luxury French, vintage-inspired fashion brand, we take pride in the presentation of our products, and we believe that a stylish and branded packing satchel will enhance our customers' experience.

We are looking for a design that incorporates our company logo, ‘Renard Céleste’ while being very feminine and French-inspired. The satchel should be practical, with a section (10.4cm x 16.5cm) for the shipping label to be placed onto the bag without it covering any logos. We are open to different colours, and designs, as long as they align with our brand image.

The packing satchel will be used to ship our products to customers worldwide, so we need a versatile design that can accommodate different-sized packing satchels.

To gain further inspiration on what type of brand Renard Céleste is please visit our website https://renardceleste.example/.

Some ideas I have attached in the images below:
- Quirky
- Looks like old mail
- Has a feel-good written phrase on the back of the packaging
- Looks vintage and unique

```html
<!DOCTYPE html>
<html lang="en">
<head>
<meta charset="UTF-8">
<title>Renard Céleste – Mailer Bag</title>
<link rel="stylesheet" href="https://fonts.googleapis.com/css2?family=Almendra+SC&family=Almendra:wght@700&family=Roboto:wght@400&display=swap">
<style>
  :root {
    --backdrop: #808080;
    --frame: #e3d2b4;
    --frame-edge: #d8c39f;
    --paper: #f2eee4;
    --paper-light: #f7f4ec;
    --label: #faf6ec;
    --perforation: #ecdcc6;
    --ink: #161414;
  }
  html, body {
    margin: 0;
    padding: 0;
    width: 1200px;
    height: 877px;
    overflow: hidden;
    background: var(--backdrop);
  }
  .mailer {
    position: absolute;
    left: 347px;
    top: 38px;
    width: 505px;
    height: 800px;
    background: linear-gradient(135deg, var(--frame-edge), var(--frame) 40%, var(--frame-edge));
    box-shadow: 10px 12px 6px rgba(0,0,0,0.22);
  }
  .mailer__paper {
    position: absolute;
    inset: 16px 18px 16px 18px;
    background: radial-gradient(ellipse at 50% 45%, var(--paper-light) 0%, var(--paper) 70%, #ebe4d6 100%);
  }
  .address-label {
    position: absolute;
    left: 24px;
    top: 20px;
    width: 271px;
    height: 186px;
  }
  .address-label svg { position: absolute; inset: 0; }
  .address-label__title {
    position: absolute;
    left: 28px;
    top: 22px;
    font-family: "Almendra", serif;
    font-weight: 700;
    font-size: 21px;
    color: var(--ink);
    margin: 0;
  }
  .brand-name {
    position: absolute;
    left: 0;
    right: 0;
    top: 320px;
    margin: 0;
    text-align: center;
    font-family: "Almendra SC", serif;
    font-weight: 400;
    font-size: 46px;
    letter-spacing: 1px;
    color: var(--ink);
  }
  .contact {
    position: absolute;
    left: 0;
    right: 0;
    top: 445px;
    text-align: center;
    color: var(--ink);
  }
  .contact__icon { display: block; margin: 0 auto; }
  .contact__heading {
    margin: 10px 0 0;
    font-family: "Almendra", serif;
    font-weight: 700;
    font-size: 22px;
  }
  .contact__email {
    margin: 6px 0 0;
    font-family: "Roboto", sans-serif;
    font-size: 17px;
  }
</style>
</head>
<body>
  <main class="mailer">
    <div class="mailer__paper">
      <section class="address-label">
        <svg width="271" height="186" viewBox="0 0 271 186" aria-hidden="true">
          <rect x="3" y="3" width="265" height="180" fill="var(--label)" stroke="var(--perforation)" stroke-width="5" stroke-dasharray="0 6" stroke-linecap="round"/>
        </svg>
        <p class="address-label__title">TO</p>
      </section>

      <h1 class="brand-name">Renard Céleste</h1>

      <section class="contact">
        <svg class="contact__icon" width="42" height="42" viewBox="0 0 42 42" aria-hidden="true">
          <circle cx="21" cy="21" r="18.5" fill="none" stroke="var(--ink)" stroke-width="3"/>
          <rect x="11" y="14" width="20" height="14" rx="1.5" fill="var(--ink)"/>
          <path d="M11.5 14.5 L21 22 L30.5 14.5 M11.5 27.5 L18 21 M30.5 27.5 L24 21" fill="none" stroke="var(--paper)" stroke-width="1.6"/>
        </svg>
        <p class="contact__heading">Customer Service</p>
        <p class="contact__email">E-mail: online@renardceleste.example</p>
      </section>
    </div>
  </main>
</body>
</html>
```